Pop Up Banner Design (30x72in) for events for Orbis Tongue Academy

30 x 72 inch design for a pop up banner or 2 (or 3) to advertise my business, Orbis Tongue Academy, featuring www.orbistongueacademy.com

This banner will be used at anime conventions, or local events to promote the business to the general public, schools, or asian culture lovers.

Color scheme to identify with the logo that is attached. Imagery would be great!

Target audience: teens to 30s
Benefits OTA Offers: learning japanese language, learning japanese culture, peer study groups and events, one-on-one or classroom setting, in person or virtual learning, Kestrel Fluency Grading Exam (KFGE) preparation, homework, guided tours to Japan once a year, translation services, conversation tables, etc.

Target Market(s)

teens to 30 year olds

Industry/Entity Type

Education

Font styles to use
Sans Serif

Colors
ec1f27
ffffff
000000

Requirements
Must have
• logo, imagery, benefits strategically explained, website

```html
<!DOCTYPE html>
<html lang="en">
<head>
<meta charset="utf-8">
<title>Orbis Tongue Academy – Pop Up Banner</title>
<link href="https://fonts.googleapis.com/css2?family=Arimo:wght@700&family=Roboto+Condensed:wght@400&display=swap" rel="stylesheet">
<style>
  :root {
    --brand-red: #c82a2b;
    --deep-red: #b51f22;
    --white: #ffffff;
    --ink: #1a1a1a;
    --gold: #f7c400;
    --orange: #ec7a1c;
    --photo-dark: #3e4650;
    --photo-light: #8e96a0;
  }
  html, body {
    margin: 0;
    padding: 0;
    width: 1200px;
    height: 2878px;
    overflow: hidden;
    background: var(--white);
  }
  .banner {
    position: relative;
    width: 1200px;
    height: 2878px;
    overflow: hidden;
    background: var(--white);
  }
  .banner-art {
    position: absolute;
    inset: 0;
    width: 1200px;
    height: 2878px;
  }
  .brand {
    position: absolute;
    top: 105px;
    left: 0;
    width: 1200px;
    text-align: center;
  }
  .brand-dot {
    width: 300px;
    height: 300px;
    margin: 0 auto 60px;
    border-radius: 50%;
    background: var(--brand-red);
  }
  .brand-name {
    margin: 0;
    font-family: "Roboto Condensed", sans-serif;
    font-weight: 400;
    font-size: 70px;
    line-height: 1;
    color: var(--ink);
    letter-spacing: 1px;
  }
  .brand-url {
    margin: 34px 0 0;
    font-family: "Arimo", sans-serif;
    font-weight: 700;
    font-size: 38px;
    color: var(--ink);
  }
  .section-title {
    position: absolute;
    left: 58px;
    width: 1055px;
    height: 72px;
    margin: 0;
    padding-left: 16px;
    box-sizing: border-box;
    background: linear-gradient(90deg, var(--gold) 0%, #f5b400 45%, var(--orange) 80%, rgba(236,122,28,0) 100%);
    font-family: "Arimo", sans-serif;
    font-weight: 700;
    font-size: 42px;
    line-height: 72px;
    color: var(--ink);
    white-space: nowrap;
  }
  .section-title.benefits { top: 2112px; }
  .section-title.exam { top: 2550px; font-size: 38px; }
  .bullet-list {
    position: absolute;
    left: 60px;
    margin: 0;
    padding: 0;
    list-style: none;
    font-family: "Roboto Condensed", sans-serif;
    font-size: 45px;
    line-height: 62px;
    color: var(--white);
  }
  .bullet-list li::before {
    content: "•";
    margin-right: 18px;
  }
  .bullet-list.benefits { top: 2196px; }
  .bullet-list.exam { top: 2634px; }
  .bullet-list .pair::before { content: none; }
  .bullet-list .pair span::before {
    content: "•";
    margin-right: 18px;
  }
  .bullet-list .pair span + span { margin-left: 18px; }
</style>
</head>
<body>
<div class="banner">
  <svg class="banner-art" viewBox="0 0 1200 2878" xmlns="http://www.w3.org/2000/svg">
    <defs>
      <linearGradient id="photoTone" x1="0" y1="0" x2="1" y2="1">
        <stop offset="0" stop-color="var(--photo-light)"/>
        <stop offset="0.5" stop-color="var(--photo-dark)"/>
        <stop offset="1" stop-color="#6e7680"/>
      </linearGradient>
      <linearGradient id="swooshTop" x1="0" y1="0" x2="1" y2="0">
        <stop offset="0" stop-color="#f7c400"/>
        <stop offset="0.55" stop-color="#ec7a1c"/>
        <stop offset="1" stop-color="#d4262a"/>
      </linearGradient>
      <linearGradient id="swooshBottom" x1="0" y1="0" x2="1" y2="0">
        <stop offset="0" stop-color="#d4262a"/>
        <stop offset="0.5" stop-color="#ec7a1c"/>
        <stop offset="1" stop-color="#f7c400"/>
      </linearGradient>
    </defs>
    <path d="M0 1000 Q600 760 1200 775 L1200 1730 Q650 1960 0 2010 Z" fill="url(#photoTone)" role="img" aria-label="Photo of a smiling group of young students huddled in a circle, seen from above"/>
    <path d="M0 985 Q560 725 1200 730 L1200 790 Q600 775 0 1015 Z" fill="url(#swooshTop)"/>
    <path d="M0 2000 Q650 1950 1200 1715 L1200 2878 L0 2878 Z" fill="var(--brand-red)"/>
    <path d="M0 2000 Q700 1930 1200 1710 L1200 1790 Q650 1990 0 2040 Z" fill="url(#swooshBottom)"/>
    <path d="M0 2040 Q650 1990 1200 1790 L1200 1830 Q650 2025 0 2060 Z" fill="var(--deep-red)"/>
  </svg>

  <header class="brand">
    <div class="brand-dot"></div>
    <h1 class="brand-name">ORBIS TONGUE ACADEMY</h1>
    <p class="brand-url">www.orbistongueacademy.com</p>
  </header>

  <h2 class="section-title benefits">Benefits OTA Offers:</h2>
  <ul class="bullet-list benefits">
    <li>Learning Japanese Language</li>
    <li>Learning Japanese Culture</li>
    <li>Peer Study Groups And Events</li>
    <li>One-on-one Or Classroom Setting</li>
    <li>In Person Or Virtual Learning</li>
  </ul>

  <h2 class="section-title exam">Kestrel Fluency Grading Exam (KFGE)</h2>
  <ul class="bullet-list exam">
    <li class="pair"><span>Preparation</span><span>Homework</span></li>
    <li>Guided tours to Japan once a year</li>
    <li class="pair"><span>Translation Services</span><span>Conversation Tables, etc.</span></li>
  </ul>
</div>
</body>
</html>
```